Commercial and Residential Paint Contractor needs website

We need a website for our residential painting, multi-family painting and commercial painting company. We paint interior and exterior of houses, apartments and commercial buildings. I would like an about us page, residential page, multi family page, commercial page and contact us. Need keywords added to website for seo opitimazation. I like this website https://www.wallcraftcrew.com/

Target Market(s)

General Contractors and commercial property managers

Coding

Coded - Design and coding required

Number of Pages Required

5+ page

Font styles to use
Sans Serif

Requirements
Must have
• I need SEO keywords on pages

```html
<!DOCTYPE html>
<html lang="en">
<head>
<meta charset="utf-8">
<title>Crestline Painting – Residential, Multi-Family &amp; Commercial Painting</title>
<meta name="description" content="Crestline Painting: interior and exterior residential, multi-family and commercial painting contractor in Texas.">
<link href="https://fonts.googleapis.com/css2?family=Poppins:wght@400;500;600&family=Open+Sans:wght@400;600&display=swap" rel="stylesheet">
<style>
:root{
  --navy:#1b3f8b;
  --red:#c4172c;
  --red-band:#c41a30;
  --blue-band:#1e4b9e;
  --ink:#333;
  --muted:#555;
  --dark:#262626;
  --white:#fff;
  --star:#f7941d;
}
*{box-sizing:border-box;margin:0;padding:0}
html,body{width:1200px;height:3434px;overflow:hidden;background:var(--white)}
body{position:relative;font-family:"Open Sans",Arial,sans-serif;color:var(--ink)}
.abs{position:absolute}
h1,h2,h3,.nav a,.brand,.phone,.btn,.name{font-family:"Poppins",Arial,sans-serif}

/* header */
.brand{left:145px;top:30px;font-size:38px;font-weight:600;color:var(--navy);line-height:1;display:flex;align-items:center;gap:10px}
.brand-mark{width:18px;height:18px;background:var(--red)}
.address{left:662px;top:22px;display:flex;gap:10px;align-items:center;font-size:11px;color:var(--red);line-height:17px}
.phone{left:870px;top:20px;display:flex;gap:10px;align-items:center;font-size:25px;color:var(--red);font-weight:500}
.nav{left:459px;top:66px;display:flex;gap:40px}
.nav a{text-decoration:none;color:#444;font-size:16px}
.nav a.active{color:var(--navy)}

/* hero */
.hero{left:0;top:120px;width:1200px;height:500px;background:linear-gradient(100deg,#7d8fb3 0%,#d6cfc4 22%,#cfc5b7 55%,#b9ae9f 80%,#8fa0c2 100%);clip-path:polygon(0 4px,20% 0,45% 5px,70% 1px,100% 5px,100% 99%,80% 100%,50% 98.6%,25% 100%,0 99%)}
.arrow{width:56px;height:56px;border-radius:50%;background:var(--navy);display:flex;align-items:center;justify-content:center}
.arrow.light{background:transparent}

/* welcome */
.welcome h1{left:144px;top:695px;font-size:34px;font-weight:600;color:var(--navy)}
.welcome p{left:144px;top:750px;width:525px;font-size:13.3px;line-height:27.2px;color:var(--muted)}
.btn{display:flex;align-items:center;justify-content:center;font-size:12.5px;text-transform:uppercase;text-decoration:none}
.btn.solid{background:var(--red);color:var(--white);border-radius:2px}
.btn.outline{border:1px solid var(--red);color:var(--red);border-radius:2px;background:var(--white)}
.splash{left:735px;top:705px;width:320px;height:285px;background:radial-gradient(ellipse at center,#b59a7c 0%,#d9cdb8 60%,#fff 72%);border-radius:42% 58% 50% 50%/45% 50% 55% 55%}

/* bands */
.band{left:0;width:1200px}
.band.red{top:1083px;height:500px;background:var(--red-band);clip-path:polygon(0 4px,30% 1px,60% 5px,100% 0,100% 99%,70% 100%,35% 98.8%,0 100%)}
.band.blue{top:2317px;height:540px;background:var(--blue-band);clip-path:polygon(0 3px,25% 0,55% 5px,100% 1px,100% 99%,65% 100%,30% 98.8%,0 100%)}
.band-title{width:1200px;left:0;text-align:center;color:var(--white);font-size:34px;font-weight:500}
.section-title{width:1200px;left:0;text-align:center;color:var(--navy);font-size:34px;font-weight:600}

/* cards */
.card{background:var(--white);width:297px;text-align:center}
.service{top:1265px;height:247px}
.service h3{margin-top:64px;font-size:25px;font-weight:500;color:var(--red)}
.service p{margin:14px auto 0;width:262px;font-size:10.5px;line-height:20.5px;color:var(--ink)}
.service .btn{margin:16px auto 0;width:105px;height:40px}
.icon-ring{width:112px;height:112px;border-radius:50%;background:var(--white);display:flex;align-items:center;justify-content:center}
.icon-dot{width:96px;height:96px;border-radius:50%;background:#222;display:flex;align-items:center;justify-content:center}

/* works */
.photo{display:block}
.review{top:2558px;height:223px}
.review p{margin:70px auto 0;width:262px;font-size:13px;line-height:25.6px;color:#333}
.review .name{margin-top:6px;font-size:20px;color:var(--red)}
.avatar{width:112px;height:112px;border-radius:50%;background:var(--white);display:flex;align-items:center;justify-content:center}
.avatar span{width:98px;height:98px;border-radius:50%;display:block}

/* quote */
.field{border:1px solid #999;background:var(--white);font-size:11px;color:#444;padding:12px 14px}

/* footer */
.footer{left:0;top:3265px;width:1200px;height:169px;background:var(--dark);clip-path:polygon(0 4px,35% 0,65% 5px,100% 1px,100% 100%,0 100%)}
.foot-links{left:144px;top:3325px;font-size:13px;color:#ddd;display:flex;gap:11px}
.foot-links a{color:#ddd;text-decoration:none}
.copyright{left:144px;top:3365px;font-size:13px;color:#ddd}
.social{top:3340px;width:28px;height:28px;border:2px solid #ddd;border-radius:50%}
</style>
</head>
<body>

<header>
  <div class="abs brand"><span class="brand-mark"></span>Crestline Painting</div>
  <div class="abs address">
    <svg width="26" height="26" viewBox="0 0 26 26"><circle cx="13" cy="13" r="13" fill="#c4172c"/><path d="M13 6a5 5 0 0 0-5 5c0 4 5 9 5 9s5-5 5-9a5 5 0 0 0-5-5z" fill="#fff"/><circle cx="13" cy="11" r="2" fill="#c4172c"/></svg>
    <div>482 Alder Ave, Ste 12<br>Maple Grove, Texas 75990, US</div>
  </div>
  <div class="abs phone">
    <svg width="26" height="26" viewBox="0 0 26 26"><circle cx="13" cy="13" r="13" fill="#c4172c"/><path d="M9 7l3 3-1.6 1.6a9 9 0 0 0 4 4L16 14l3 3-1.8 1.8C12 18.5 7.5 14 7.2 8.8z" fill="#fff"/></svg>
    555 214 7730
  </div>
  <nav class="abs nav">
    <a href="#" class="active">About Us</a><a href="#">Residential</a><a href="#">Multi Family</a><a href="#">Commercial</a><a href="#">Contact Us</a>
  </nav>
</header>

<section>
  <div class="abs hero" role="img" aria-label="Painter in white overalls painting the exterior trim of a beige house with brown shutters"></div>
  <div class="abs arrow" style="left:48px;top:347px"><svg width="18" height="18" viewBox="0 0 18 18"><path d="M12 2L5 9l7 7" stroke="#fff" stroke-width="3" fill="none"/></svg></div>
  <div class="abs arrow" style="left:1094px;top:347px"><svg width="18" height="18" viewBox="0 0 18 18"><path d="M6 2l7 7-7 7" stroke="#fff" stroke-width="3" fill="none"/></svg></div>
</section>

<section class="welcome">
  <h1 class="abs">Welcome to Crestline Painting</h1>
  <p class="abs">Fusce sollicitudin lorem et luctus volutpat. Proin placerat dapibus gravida. In tristique tristique nulla eget hendrerit. Maecenas vel tortor accumsan quam varius imperdiet vel eget elit. Aenean facilisis tincidunt lectus, id dictum nisi luctus eget. Vivamus efficitur ex condimentum, malesuada eros eget, feugiat nibh. Sed tellus ex, imperdiet eget gravida sit amet, volutpat eget turpis. In nec ultricies est. Etiam mattis augue vehicula odio posuere, sit amet tempus.</p>
  <a href="#" class="abs btn solid" style="left:144px;top:932px;width:104px;height:40px">Read More</a>
  <div class="abs splash" role="img" aria-label="Paint-splash framed photo of a painter rolling white paint under a roof eave"></div>
</section>

<section>
  <div class="abs band red"></div>
  <h2 class="abs band-title" style="top:1145px">Our Services</h2>

  <div class="abs card service" style="left:144px">
    <h3>Residential Painting</h3>
    <p>Pellentesque convallis molestie enim amet efficitur. Etiam id imperdiet lectus. Vivamus lacus justo, ultrices nec erat bibendum tellus.</p>
    <a href="#" class="btn outline">Read More</a>
  </div>
  <div class="abs card service" style="left:451px">
    <h3>Multi-family Painting</h3>
    <p>Pellentesque convallis molestie enim amet efficitur. Etiam id imperdiet lectus. Vivamus lacus justo, ultrices nec erat bibendum tellus.</p>
    <a href="#" class="btn outline">Read More</a>
  </div>
  <div class="abs card service" style="left:758px">
    <h3>Commercial Painting</h3>
    <p>Pellentesque convallis molestie enim amet efficitur. Etiam id imperdiet lectus. Vivamus lacus justo, ultrices nec erat bibendum tellus.</p>
    <a href="#" class="btn outline">Read More</a>
  </div>

  <div class="abs icon-ring" style="left:236px;top:1207px"><div class="icon-dot">
    <svg width="48" height="48" viewBox="0 0 48 48" fill="none" stroke="#fff" stroke-width="2"><path d="M6 24L24 9l18 15"/><path d="M11 20v19h26V20"/><rect x="17" y="28" width="6" height="11"/><rect x="27" y="27" width="6" height="6"/></svg>
  </div></div>
  <div class="abs icon-ring" style="left:544px;top:1207px"><div class="icon-dot">
    <svg width="48" height="48" viewBox="0 0 48 48" fill="none" stroke="#fff" stroke-width="2"><rect x="20" y="8" width="18" height="10" transform="rotate(40 29 13)"/><path d="M22 20L10 34"/><path d="M8 32l4 4-4 4-4-4z"/><path d="M34 20v12h-6v8"/></svg>
  </div></div>
  <div class="abs icon-ring" style="left:851px;top:1207px"><div class="icon-dot">
    <svg width="48" height="48" viewBox="0 0 48 48" fill="none" stroke="#fff" stroke-width="2"><rect x="14" y="8" width="20" height="32"/><path d="M18 13h3M27 13h3M18 19h3M27 19h3M18 25h3M27 25h3"/><rect x="21" y="32" width="6" height="8"/><path d="M8 40h32"/></svg>
  </div></div>
</section>

<section>
  <h2 class="abs section-title" style="top:1657px">Our Works</h2>
  <div class="abs photo" style="left:144px;top:1717px;width:516px;height:208px;background:linear-gradient(120deg,#c98a4c,#e6b777 45%,#2c9cc4 75%,#1d3e6e)" role="img" aria-label="Covered patio with lounge chairs beside a lit swimming pool at dusk"></div>
  <div class="abs photo" style="left:144px;top:1934px;width:253px;height:207px;background:linear-gradient(180deg,#7fb0dc,#3f7a3a 55%,#c9b99a)" role="img" aria-label="Mediterranean style home with tile roof framed by oak trees and a garden path"></div>
  <div class="abs photo" style="left:406px;top:1934px;width:254px;height:207px;background:linear-gradient(135deg,#d79a5a,#a8764a 50%,#3ea0b8)" role="img" aria-label="Outdoor living room with wicker seating overlooking a pool"></div>
  <div class="abs photo" style="left:667px;top:1717px;width:389px;height:424px;background:linear-gradient(180deg,#e3e8ef,#8b8f96 45%,#6e6b68 70%,#5fa040 88%,#c7c7c7)" role="img" aria-label="Two-story gray craftsman house with a double garage and front lawn"></div>
  <a href="#" class="abs btn solid" style="left:548px;top:2165px;width:104px;height:40px">View All</a>
</section>

<section>
  <div class="abs band blue"></div>
  <h2 class="abs band-title" style="top:2387px">Reviews</h2>
  <svg class="abs" style="left:505px;top:2443px" width="190" height="34" viewBox="0 0 190 34">
    <defs><path id="star" d="M17 1l4.8 10.2 11.2 1.3-8.3 7.6 2.3 11L17 25.6 7 31.1l2.3-11L1 12.5l11.2-1.3z"/></defs>
    <use href="#star" fill="#f7941d"/><use href="#star" x="38" fill="#f7941d"/><use href="#star" x="76" fill="#f7941d"/><use href="#star" x="114" fill="#f7941d"/><use href="#star" x="152" fill="#f7941d"/>
  </svg>

  <div class="abs card review" style="left:144px">
    <p>“ Quisque aliquet ex nec est vestibulum pulvinar. Pellentesque convallis molestie enim amet efficitur. Etiam id imperdiet lectus ultrices nec erat. ”</p>
    <div class="name">Dean Harlow</div>
  </div>
  <div class="abs card review" style="left:451px">
    <p>“ Vivamus eleifend vitae nulla vel malesuada. In ac malesuada lacus, et consectetur ante. Fusce vitae lectus sit amet mi pulvinar maximus. ”</p>
    <div class="name">Nora</div>
  </div>
  <div class="abs card review" style="left:758px">
    <p>“ Phasellus nisl est, condimentum vitae faucibus metus. Nunc amet sit amet consequat risus. Curabitur orci ac elit leo. In eleifend dui tellus.</p>
    <div class="name">Marco</div>
  </div>

  <div class="abs avatar" style="left:236px;top:2502px"><span style="background:linear-gradient(#d8d8d8,#9a9a9a)" role="img" aria-label="Reviewer portrait"></span></div>
  <div class="abs avatar" style="left:544px;top:2502px"><span style="background:linear-gradient(#e6dccb,#b89a76)" role="img" aria-label="Reviewer portrait"></span></div>
  <div class="abs avatar" style="left:851px;top:2502px"><span style="background:linear-gradient(#dcdcdc,#7c7064)" role="img" aria-label="Reviewer portrait"></span></div>

  <div class="abs arrow light" style="left:48px;top:2642px"><svg width="20" height="24" viewBox="0 0 20 24"><path d="M14 2L5 12l9 10" stroke="#fff" stroke-width="3" fill="none"/></svg></div>
  <div class="abs arrow light" style="left:1094px;top:2642px"><svg width="20" height="24" viewBox="0 0 20 24"><path d="M6 2l9 10-9 10" stroke="#fff" stroke-width="3" fill="none"/></svg></div>
</section>

<section>
  <h2 class="abs section-title" style="top:2935px">Get a Quick Quote</h2>
  <div class="abs field" style="left:144px;top:3000px;width:217px;height:40px">Name</div>
  <div class="abs field" style="left:376px;top:3000px;width:217px;height:40px">Email</div>
  <div class="abs field" style="left:144px;top:3055px;width:217px;height:40px">Phone</div>
  <div class="abs field" style="left:376px;top:3055px;width:217px;height:40px">Address</div>
  <div class="abs field" style="left:606px;top:3000px;width:450px;height:95px">Message</div>
  <a href="#" class="abs btn solid" style="left:548px;top:3115px;width:104px;height:40px">Submit</a>
</section>

<footer>
  <div class="abs footer"></div>
  <div class="abs foot-links"><a href="#">Home</a>|<a href="#">About Us</a>|<a href="#">Residential</a>|<a href="#">Multi Family</a>|<a href="#">Commercial</a>|<a href="#">Contact Us</a></div>
  <div class="abs copyright">Copyright © 2020&nbsp;&nbsp;Crestline Painting.&nbsp;&nbsp;&nbsp;All rights reserved.</div>
  <a href="#" class="abs social" style="left:920px" aria-label="Social profile"></a>
  <a href="#" class="abs social" style="left:970px" aria-label="Social profile"></a>
  <a href="#" class="abs social" style="left:1028px" aria-label="Social profile"></a>
</footer>

</body>
</html>
```